Verodex business card

Business card for sustainable investment company called "Verodex". Verodex is an exchange platform selling carbon credits between buyers and sellers. Carbon Credits are an environmental commodity for reducing global carbon emissions.

the card should obviously have our logo and the theme should be sustainability/environment mixed with a trading platform.

Contact Information for Business Card

Logo, Name, Title, Phone, Email

Colors
0054AA
0677BA
7BADD7
CADEEF
E8F1F8
0094D4
00A9DD
6FCCEA
C7EBF8
E9F6FB
00AB8E
00BBA5
67D7C9
C6EFE9
E9F9F6
59FF00
82FF00
B8FF75
E3FFCB
F4FFEA

```html
<!DOCTYPE html>
<html lang="en">
<head>
<meta charset="utf-8">
<title>Verodex business card</title>
<link rel="stylesheet" href="https://fonts.googleapis.com/css2?family=Urbanist:wght@400;500;700;800&display=swap">
<style>
  :root {
    --backdrop: #e4e4e4;
    --navy-deep: #1b2b48;
    --navy: #243a5e;
    --navy-ink: #1d2a45;
    --paper: #f3f3f3;
    --paper-shade: #e9e9e9;
    --teal: #4fb8d2;
    --blue: #2f6fc4;
    --name-blue: #3c9fcf;
    --icon-blue: #2f7fc6;
  }
  * { box-sizing: border-box; margin: 0; padding: 0; }
  html, body {
    width: 1200px; height: 1200px; overflow: hidden;
    background: var(--backdrop);
    font-family: "Urbanist", sans-serif;
    color: var(--navy-ink);
  }
  .card {
    position: absolute;
    left: 234px;
    width: 730px;
    height: 418px;
    box-shadow: 0 14px 28px rgba(0,0,0,0.22);
  }
  .card-front {
    top: 160px;
    overflow: hidden;
  }
  .front-pattern {
    position: absolute; inset: 0;
    background: linear-gradient(160deg, var(--navy) 0%, var(--navy-deep) 100%);
  }
  .front-wordmark {
    position: absolute;
    left: 0; right: 0; top: 188px;
    text-align: center;
    font-size: 42px;
    font-weight: 700;
    color: #ffffff;
    letter-spacing: 1px;
  }
  .card-back {
    top: 632px;
    background: linear-gradient(120deg, var(--paper) 0%, var(--paper-shade) 55%, var(--paper) 100%);
  }
  .brand {
    position: absolute;
    left: 51px; top: 52px;
    display: flex; align-items: center; gap: 14px;
  }
  .brand-mark {
    width: 34px; height: 34px;
    background: var(--blue);
  }
  .brand-name {
    font-size: 44px;
    font-weight: 700;
    color: var(--navy-ink);
    letter-spacing: 0.5px;
  }
  .person {
    position: absolute;
    right: 51px; top: 50px;
    text-align: right;
  }
  .person-name {
    font-size: 37px;
    font-weight: 800;
    color: var(--name-blue);
    line-height: 1;
  }
  .person-title {
    margin-top: 6px;
    font-size: 20px;
    font-weight: 500;
    color: var(--navy-ink);
  }
  .edge-tab {
    position: absolute;
    right: 0; top: 52px;
    width: 29px; height: 58px;
    background: linear-gradient(90deg, var(--teal), var(--blue));
  }
  .contacts {
    position: absolute;
    left: 51px; top: 287px;
    list-style: none;
    font-size: 21px;
    font-weight: 500;
  }
  .contacts li {
    display: flex; align-items: center; gap: 9px;
    height: 28px;
  }
  .contacts svg { width: 15px; height: 15px; flex: none; }
  .office {
    position: absolute;
    right: 51px; top: 287px;
    text-align: right;
    font-size: 21px;
    font-weight: 500;
    font-style: normal;
  }
  .office span { display: block; height: 28px; line-height: 28px; }
  .office .office-name { font-weight: 700; }
  .contacts li { line-height: 28px; }
</style>
</head>
<body>
  <section class="card card-front">
    <div class="front-pattern" role="img" aria-label="Tiled pattern of embossed brand symbols on deep navy"></div>
    <div class="front-wordmark">Verodex</div>
  </section>

  <section class="card card-back">
    <div class="brand">
      <div class="brand-mark"></div>
      <div class="brand-name">VERODEX</div>
    </div>

    <div class="person">
      <div class="person-name">Mark Halden</div>
      <div class="person-title">Sales Representative</div>
    </div>
    <div class="edge-tab"></div>

    <ul class="contacts">
      <li>
        <svg viewBox="0 0 16 16"><path fill="var(--icon-blue)" d="M3.6 1.5l2.3 2.6-1.2 1.7c.8 2 2.3 3.6 4.4 4.6l1.7-1.2 2.6 2.3-1.4 2.2C6.6 15.2.8 9.4 1.3 3l2.3-1.5z"/><path d="M10 1.5a4.5 4.5 0 0 1 4.5 4.5M10 4a2 2 0 0 1 2 2" stroke="var(--icon-blue)" stroke-width="1.3" fill="none"/></svg>
        +36 30 412 7590
      </li>
      <li>
        <svg viewBox="0 0 16 16"><rect x="1" y="3" width="14" height="10" rx="1" fill="var(--icon-blue)"/><path d="M1.5 4l6.5 5 6.5-5" stroke="#fff" stroke-width="1.3" fill="none"/></svg>
        szerviz@verodex.com
      </li>
      <li>
        <svg viewBox="0 0 16 16" fill="none" stroke="var(--icon-blue)" stroke-width="1.4"><circle cx="8" cy="8" r="6.5"/><ellipse cx="8" cy="8" rx="2.8" ry="6.5"/><path d="M1.5 8h13"/></svg>
        www.verodex.com
      </li>
    </ul>

    <address class="office">
      <span class="office-name">Verodex Head Office</span>
      <span>Budapest XI.</span>
      <span>Fehérvári út 18.</span>
    </address>
  </section>
</body>
</html>
```